Income Tax Business Cards - Updates

Need to update these business cards while keeping all the same wording but just update them and make them look nicer and more modern/ on brand with our brand.

Industry/Entity Type

finance

Contact Information for Business Card

we have multiple locations so will just need to easily be able to change the address and phone numbers

Colors

Designer to choose colors to be used in the design.

```html
<!DOCTYPE html>
<html lang="en">
<head>
<meta charset="utf-8">
<title>Ledgerline Financial Group – Business Cards</title>
<link href="https://fonts.googleapis.com/css2?family=Montserrat:wght@400;500;600;700;800&display=swap" rel="stylesheet">
<style>
  :root {
    --brand-green: #0f5130;
    --brand-red: #c41e2a;
    --paper: #ffffff;
    --backdrop: #e9eae8;
    --ink-soft: #3a3a3a;
    --tint-green: #eef2ef;
  }
  * { box-sizing: border-box; margin: 0; padding: 0; }
  html, body { width: 1200px; height: 948px; overflow: hidden; }
  body {
    background: var(--backdrop);
    font-family: "Montserrat", sans-serif;
    position: relative;
  }
  .card {
    position: absolute;
    left: 250px;
    width: 700px;
    height: 400px;
    border-radius: 24px;
    overflow: hidden;
    box-shadow: 0 14px 34px rgba(0,0,0,.18);
  }
  .brand-name {
    font-weight: 700; letter-spacing: .5px;
    display: inline-flex; align-items: center; white-space: nowrap;
  }
  .brand-dot { border-radius: 50%; background: currentColor; display: inline-block; flex: none; }
  .amount { color: var(--brand-red); }

  /* Front side */
  .card-front { top: 44px; background: var(--brand-green); color: var(--paper); }
  .front-brand {
    position: absolute; top: 84px; left: 0; width: 100%;
    text-align: center;
  }
  .front-brand .brand-name { font-size: 38px; gap: 14px; }
  .front-brand .brand-dot { width: 18px; height: 18px; }
  .file-pill {
    position: absolute; top: 196px; left: 50%; transform: translateX(-50%);
    background: var(--brand-red); color: var(--paper);
    font-weight: 700; font-size: 17px; letter-spacing: 1px;
    padding: 9px 26px; border-radius: 30px; white-space: nowrap;
  }
  .front-offer {
    position: absolute; top: 272px; left: 30px; right: 30px;
    text-align: center; font-weight: 800; font-size: 28px; letter-spacing: 1px;
    white-space: nowrap;
  }

  /* Back side */
  .card-back { top: 504px; background: var(--paper); }
  .back-shapes { position: absolute; inset: 0; }
  .back-offer {
    position: absolute; top: 30px; left: 300px; width: 330px;
    color: var(--brand-green); font-weight: 800;
  }
  .free-estimates { font-size: 12px; font-weight: 700; color: var(--ink-soft); letter-spacing: .8px; }
  .offer-main { font-size: 36px; line-height: 1.15; letter-spacing: 1px; white-space: nowrap; }
  .offer-sub { font-size: 23px; line-height: 1.2; letter-spacing: 1px; white-space: nowrap; }
  .offer-note { font-size: 12px; font-weight: 700; color: var(--ink-soft); letter-spacing: .8px; margin-top: 2px; }
  .back-brand {
    position: absolute; top: 160px; left: 44px;
    color: var(--brand-green);
  }
  .back-brand .brand-name { font-size: 30px; gap: 10px; }
  .back-brand .brand-dot { width: 14px; height: 14px; background: var(--brand-red); }
  .address {
    position: absolute; top: 222px; left: 46px;
    font-weight: 500; font-size: 20px; line-height: 1.35; color: var(--ink-soft);
    font-style: normal;
  }
  .phone {
    display: flex; align-items: center; gap: 10px; margin-top: 4px;
    font-weight: 700; font-size: 24px; color: var(--brand-green);
  }
  .phone svg { width: 20px; height: 20px; }
</style>
</head>
<body>

<section class="card card-front" aria-label="Card front">
  <div class="front-brand">
    <span class="brand-name"><span class="brand-dot"></span>Ledgerline Financial Group</span>
  </div>
  <div class="file-pill">FILE YOUR TAXES HERE</div>
  <p class="front-offer">UP TO <span class="amount">$6000</span> SAME DAY ADVANCE</p>
</section>

<section class="card card-back" aria-label="Card back">
  <svg class="back-shapes" viewBox="0 0 700 400" preserveAspectRatio="none" aria-hidden="true">
    <circle cx="640" cy="270" r="100" fill="var(--tint-green)"/>
    <polygon points="640,0 700,0 700,90 675,90" fill="var(--brand-red)"/>
    <polygon points="300,400 560,352 570,400" fill="var(--brand-green)"/>
    <polygon points="560,352 700,312 700,400 570,400" fill="var(--brand-red)"/>
  </svg>

  <div class="back-offer">
    <p class="free-estimates">FREE ESTIMATES!</p>
    <p class="offer-main">UP TO <span class="amount">$6000</span></p>
    <p class="offer-sub">SAME DAY ADVANCE</p>
    <p class="offer-note">ON APPROVED TAX RETURNS!</p>
  </div>

  <div class="back-brand">
    <span class="brand-name"><span class="brand-dot"></span>Ledgerline Financial Group</span>
  </div>

  <address class="address">
    118 Maple Grove Rd<br>
    Ste 410<br>
    Country Name AB 5625
    <span class="phone">
      <svg viewBox="0 0 24 24" aria-hidden="true"><path fill="#c41e2a" d="M6.6 10.8a15.1 15.1 0 0 0 6.6 6.6l2.2-2.2c.3-.3.7-.4 1-.2 1.1.4 2.3.6 3.6.6.6 0 1 .4 1 1V20c0 .6-.4 1-1 1A17 17 0 0 1 3 4c0-.6.4-1 1-1h3.5c.6 0 1 .4 1 1 0 1.3.2 2.5.6 3.6.1.3 0 .7-.2 1z"/></svg>
      (555) 555-555
    </span>
  </address>
</section>

</body>
</html>
```